Website Header Development

I am after a redesign of the Header of a website www.tlvoltaris.com.au.
This project is for the header only, and should fit in with the rest of the site
Target Market(s)
Business
Requirements
Should not have
- Over the top. Keep it simple

```html
<!DOCTYPE html>
<html lang="en">
<head>
<meta charset="utf-8">
<title>Voltaris Energy – Resource Efficiency</title>
<link href="https://fonts.googleapis.com/css2?family=Alegreya:wght@700&family=Alegreya+Sans:wght@400;700;800&display=swap" rel="stylesheet">
<style>
  :root {
    --page-bg: #ffffff;
    --band-dark: #7d9f96;
    --band-light: #a9c2bb;
    --nav-green: #2d8a3e;
    --nav-shade: #247432;
    --navy: #1b2a78;
    --heading-navy: #14236e;
    --text: #222222;
    --field-border: #c8c8c8;
    --photo-light: #e9eef2;
    --photo-mid: #c9d3db;
  }
  * { margin: 0; padding: 0; box-sizing: border-box; }
  html, body { width: 1200px; height: 678px; overflow: hidden; background: var(--page-bg); }
  body { font-family: "Alegreya Sans", sans-serif; color: var(--text); }

  .site { position: relative; width: 1000px; height: 678px; margin-left: 100px; }

  .masthead {
    position: absolute; left: 0; top: 0; width: 1000px; height: 115px;
    background: linear-gradient(100deg, var(--band-dark) 0%, var(--band-light) 55%, var(--band-dark) 100%);
    overflow: hidden;
  }
  .masthead-swoosh { position: absolute; inset: 0; }
  .brand { position: absolute; left: 40px; top: 44px; display: flex; align-items: center; gap: 12px; }
  .brand-name { font-family: "Alegreya Sans", sans-serif; font-weight: 800; font-size: 34px; color: var(--navy); letter-spacing: -0.5px; }
  .brand-mark { width: 26px; height: 26px; border-radius: 50%; background: var(--navy); }

  .main-nav { position: absolute; left: 0; top: 115px; width: 1000px; height: 52px; background: var(--nav-green); overflow: hidden; }
  .nav-shade { position: absolute; inset: 0; }
  .main-nav a {
    position: absolute; top: 0; line-height: 50px; color: #fff; text-decoration: none;
    font-size: 12.5px; font-weight: 400;
  }
  .main-nav a.nav-strong { font-size: 14.5px; font-weight: 700; line-height: 52px; }

  .page-title {
    position: absolute; left: 60px; top: 196px; width: 590px; text-align: center;
    font-family: "Alegreya", serif; font-weight: 700; font-size: 25px; color: var(--heading-navy);
  }
  .feature-photo {
    position: absolute; left: 288px; top: 259px; width: 350px; height: 233px;
    background: radial-gradient(ellipse at 65% 45%, var(--photo-mid) 0%, var(--photo-light) 70%);
  }
  .intro p { position: absolute; left: 60px; font-size: 14.5px; line-height: 25px; }

  .search-field {
    position: absolute; left: 736px; top: 168px; width: 184px; height: 31px;
    border: 1px solid var(--field-border); display: flex; align-items: center; gap: 6px; padding-left: 6px;
    font-family: Arial, sans-serif; font-size: 14px; color: #999;
  }
  .newsletter-title {
    position: absolute; left: 736px; top: 236px; width: 190px;
    font-family: "Alegreya", serif; font-weight: 700; font-size: 20px; line-height: 30px;
    letter-spacing: 2px; color: var(--heading-navy);
  }
  .newsletter-copy { position: absolute; left: 736px; width: 195px; font-size: 10.5px; font-weight: 700; line-height: 25px; }
  .newsletter-input { position: absolute; left: 736px; top: 427px; width: 183px; height: 34px; border: 1px solid #aaa; background: #fff; }
</style>
</head>
<body>
<div class="site">
  <header class="masthead">
    <svg class="masthead-swoosh" width="1000" height="115" viewBox="0 0 1000 115" aria-hidden="true">
      <path d="M300 115 C 520 60, 760 20, 1000 8 L1000 0 C 760 10, 500 50, 280 115 Z" fill="#ffffff" fill-opacity="0.22"/>
      <path d="M420 115 C 600 75, 800 45, 1000 35 L1000 115 Z" fill="#ffffff" fill-opacity="0.08"/>
    </svg>
    <div class="brand">
      <span class="brand-name">voltaris energy</span>
      <span class="brand-mark"></span>
    </div>
  </header>

  <nav class="main-nav">
    <svg class="nav-shade" width="1000" height="52" viewBox="0 0 1000 52" aria-hidden="true">
      <polygon points="0,0 235,0 268,52 0,52" fill="var(--nav-shade)" opacity="0.55"/>
      <polygon points="900,0 1000,0 1000,52 948,52" fill="var(--nav-shade)" opacity="0.55"/>
    </svg>
    <a class="nav-strong" href="#" style="left:84px">Home</a>
    <a href="#" style="left:159px">About Us</a>
    <a href="#" style="left:239px">Services</a>
    <a href="#" style="left:311px">Projects and Case Studies</a>
    <a class="nav-strong" href="#" style="left:474px">Financial Information</a>
    <a href="#" style="left:651px">News</a>
    <a href="#" style="left:711px">Contact</a>
  </nav>

  <main>
    <h1 class="page-title">Resource Efficiency – Sustainable Solutions</h1>
    <div class="feature-photo" role="img" aria-label="Photo of a businessman holding a puzzle piece labelled Solution"></div>
    <div class="intro">
      <p style="top:247px">Is your business performing as<br>well as your competitors?</p>
      <p style="top:323px">Are your fixed costs comparable<br>to industry leaders?</p>
      <p style="top:399px">Is your business becoming less<br>profitable with increased<br>energy, waste and water prices?</p>
      <p style="top:500px">Do you wish to reduce your<br>impact on the environment through reducing the use of resources (energy, waste and water)<br>within your business?</p>
    </div>
  </main>

  <aside>
    <div class="search-field">
      <svg width="14" height="14" viewBox="0 0 14 14" aria-hidden="true"><circle cx="5.5" cy="5.5" r="4" fill="none" stroke="#999" stroke-width="2"/><line x1="8.5" y1="8.5" x2="13" y2="13" stroke="#999" stroke-width="2"/></svg>
      <span>Search</span>
    </div>
    <h2 class="newsletter-title">Voltaris Energy Newsletter</h2>
    <p class="newsletter-copy" style="top:343px">Would you like to receive our regular monthly Newsletter? Please fill in your Name:</p>
    <div class="newsletter-input"></div>
    <p class="newsletter-copy" style="top:473px">Let us know your email address so we can send the Newsletter directly to your email address. (Note that your details will not be passed onto any 3rd parties. Your details stricly remain with us.)</p>
  </aside>
</div>
</body>
</html>
```